Residential Remodeling Contractor needs updated business card

I need a new design for my business card.
Name of the company is Ridgefell Construction. I need a card that commands presence, strength, integrity. I have been in business for 28 years. I am a Residential Remodeling Contractor that covers all aspects of a residential remodel and build.

```html
<!DOCTYPE html>
<html lang="en">
<head>
<meta charset="utf-8">
<title>Ridgefell Construction – Business Card</title>
<link href="https://fonts.googleapis.com/css2?family=Montserrat:wght@400;500;700;800&display=swap" rel="stylesheet">
<style>
  :root {
    --backdrop: #2b2b2d;
    --brand-blue: #213f80;
    --brand-blue-light: #2a4c94;
    --brand-blue-deep: #17305f;
    --paper: #ffffff;
    --ink: #1c1c1c;
  }
  * { box-sizing: border-box; margin: 0; padding: 0; }
  html, body {
    width: 1200px; height: 881px; overflow: hidden;
    background: var(--backdrop);
    font-family: "Montserrat", sans-serif;
  }
  .canvas {
    width: 1200px; height: 881px;
    display: flex; flex-direction: column;
    align-items: center; justify-content: center; gap: 40px;
  }
  .card {
    width: 630px; height: 360px;
    border-radius: 22px;
    position: relative;
    overflow: hidden;
  }
  .brand-mark { display: flex; align-items: center; gap: 14px; }
  .brand-mark .block { width: 22px; height: 22px; background: currentColor; flex: none; }
  .brand-name {
    font-weight: 700; text-transform: uppercase;
    letter-spacing: 2px; line-height: 1.05; white-space: nowrap;
  }

  /* Back side */
  .card-back {
    background: linear-gradient(135deg, var(--brand-blue-light), var(--brand-blue));
    display: flex; flex-direction: column;
    align-items: center; justify-content: center; gap: 34px;
  }
  .card-back .brand-mark { color: var(--brand-blue-deep); }
  .card-back .brand-name { font-size: 34px; }
  .tagline {
    color: var(--paper); font-size: 13px; font-weight: 500;
    letter-spacing: 2.5px; text-transform: uppercase;
  }

  /* Front side */
  .card-front { background: var(--paper); }
  .card-front .brand-mark {
    position: absolute; left: 40px; bottom: 70px;
    color: var(--brand-blue);
  }
  .card-front .brand-mark .block { width: 20px; height: 20px; }
  .card-front .brand-name { font-size: 20px; letter-spacing: 1px; }
  .person { position: absolute; right: 40px; top: 42px; text-align: right; }
  .person-name {
    color: var(--brand-blue); font-size: 27px; font-weight: 800;
    letter-spacing: 1.5px; text-transform: uppercase;
  }
  .person-title { color: var(--ink); font-size: 13px; margin-top: 2px; }
  .contact {
    position: absolute; right: 40px; bottom: 50px;
    text-align: right; color: var(--ink); font-size: 15px;
    list-style: none;
  }
  .contact li {
    display: flex; justify-content: flex-end; align-items: center;
    gap: 8px; line-height: 1.5; white-space: nowrap;
  }
  .contact .web-domain { color: var(--brand-blue); }
  .contact svg { width: 14px; height: 14px; flex: none; }
  .contact .address { margin-top: 12px; font-size: 15px; padding-right: 22px; }
</style>
</head>
<body>
<main class="canvas">
  <section class="card card-back" aria-label="Card back">
    <div class="brand-mark">
      <span class="block"></span>
      <span class="brand-name">Ridgefell<br>Construction</span>
    </div>
    <p class="tagline">I have been in business for 28 years</p>
  </section>

  <section class="card card-front" aria-label="Card front">
    <div class="brand-mark">
      <span class="block"></span>
      <span class="brand-name">Ridgefell<br>Construction</span>
    </div>

    <div class="person">
      <p class="person-name">Marcus Dellane</p>
      <p class="person-title">Director</p>
    </div>

    <ul class="contact">
      <li>(555) 014-2873
        <svg viewBox="0 0 24 24" fill="#213f80" aria-hidden="true"><path d="M6.6 10.8a15 15 0 0 0 6.6 6.6l2.2-2.2a1 1 0 0 1 1-.25 11.4 11.4 0 0 0 3.6.57 1 1 0 0 1 1 1V20a1 1 0 0 1-1 1A17 17 0 0 1 3 4a1 1 0 0 1 1-1h3.5a1 1 0 0 1 1 1c0 1.25.2 2.45.57 3.57a1 1 0 0 1-.25 1z"/></svg>
      </li>
      <li>info@ridgefellbuild.com
        <svg viewBox="0 0 24 24" fill="none" stroke="#213f80" stroke-width="2" aria-hidden="true"><rect x="3" y="5" width="18" height="14" rx="1"/><path d="M3 6l9 7 9-7"/></svg>
      </li>
      <li><span>www.<span class="web-domain">ridgefellbuild</span>.com</span>
        <svg viewBox="0 0 24 24" fill="none" stroke="#213f80" stroke-width="2" aria-hidden="true"><circle cx="12" cy="12" r="9"/><path d="M3 12h18M12 3c3 3 3 15 0 18M12 3c-3 3-3 15 0 18"/></svg>
      </li>
      <li class="address">42 Harrow Lane Millbrook, GA 30000</li>
    </ul>
  </section>
</main>
</body>
</html>
```